Non fiction leadership Book Cover design needed for “Stay Bold: Build On Lasting Discipline”

I need a front cover design for a new book 6 X 9 traditional non-fiction book.

Title: "Stay BOLD - Build On Lasting Discipline"

The subtitle is not finalized- so use 2 lines of smaller dummy text

My brand guide is attached (please use the tan color sparingly)

I'd like to see BOLD look like it is in motion and "flying" across the page

Need CREATIVE designs and options

Do not want my picture on the front cover - I do want it on the back cover.

On the front cover I’d like to see creative use of font to create movement on “BOLD”

Target Market(s)

Business leaders

Industry/Entity Type

Aviation

Font styles to use
Other font styles liked:
• See style guide- can add additional font (modern script or san serif)

Colors
0054AA
0677BA
7BADD7
CADEEF
E8F1F8
EB3D1F
EC4F4E
F09395
F8D3D4
FCEDEE

Requirements
Must have
• Creative font use, using perspective to create movement/motion on BOLD
Should not have
• My picture on the front cover- my picture should be on the back cover

```html
<!DOCTYPE html>
<html lang="en">
<head>
<meta charset="utf-8">
<title>Stay Bold: Build On Lasting Discipline</title>
<link href="https://fonts.googleapis.com/css2?family=Bebas+Neue&family=Montserrat:wght@500;600&display=swap" rel="stylesheet">
<style>
  :root {
    --backdrop: #03031a;
    --paper: #e2e2e2;
    --sky-blue: #1f75bc;
    --night-navy: #0a1248;
    --night-top: #4a5080;
    --ember: #e0a050;
    --light-text: #ececec;
    --craft-tint: #e6e6e6;
  }
  html, body {
    margin: 0;
    padding: 0;
    width: 1200px;
    height: 1200px;
    overflow: hidden;
    background: var(--backdrop);
  }
  .cover-canvas {
    display: block;
    width: 1200px;
    height: 1200px;
  }
  .cover-paper { fill: var(--paper); }
  .sky-shape { fill: var(--sky-blue); }
  .teaser {
    font-family: "Montserrat", sans-serif;
    font-weight: 500;
    font-size: 19px;
    fill: var(--light-text);
  }
  .aircraft-slot { fill: var(--craft-tint); }
  .title-lead {
    font-family: "Bebas Neue", sans-serif;
    font-size: 169px;
    fill: var(--sky-blue);
  }
  .title-main,
  .title-glow,
  .title-trail {
    font-family: "Bebas Neue", sans-serif;
    font-size: 690px;
  }
  .title-main {
    fill: url(#nightFill);
    stroke: var(--night-navy);
    stroke-width: 4px;
  }
  .title-glow { fill: url(#emberGlow); }
  .title-trail { fill: var(--night-navy); }
  .trail-far { opacity: 0.1; }
  .trail-near { opacity: 0.22; }
  .speed-line {
    stroke: var(--night-navy);
    stroke-linecap: round;
  }
  .subtitle-band { fill: var(--night-navy); }
  .subtitle-text {
    font-family: "Montserrat", sans-serif;
    font-weight: 600;
    font-size: 38px;
    fill: var(--light-text);
  }
  .author-name {
    font-family: "Montserrat", sans-serif;
    font-weight: 600;
    font-size: 50px;
    fill: var(--sky-blue);
  }
</style>
</head>
<body>
<svg class="cover-canvas" viewBox="0 0 1458 1458" xmlns="http://www.w3.org/2000/svg">
  <defs>
    <linearGradient id="nightFill" x1="0" y1="0" x2="0" y2="1">
      <stop offset="0" stop-color="#4a5080"/>
      <stop offset="0.22" stop-color="#0a1248"/>
      <stop offset="0.7" stop-color="#0c1450"/>
      <stop offset="1" stop-color="#2a2448"/>
    </linearGradient>
    <radialGradient id="emberGlow" cx="0.55" cy="0.95" r="0.6">
      <stop offset="0" stop-color="#e0a050" stop-opacity="0.75"/>
      <stop offset="0.35" stop-color="#b07040" stop-opacity="0.35"/>
      <stop offset="1" stop-color="#0a1248" stop-opacity="0"/>
    </radialGradient>
    <linearGradient id="lineFade" x1="0" y1="0" x2="1" y2="0">
      <stop offset="0" stop-color="#0a1248" stop-opacity="0"/>
      <stop offset="1" stop-color="#0a1248" stop-opacity="0.8"/>
    </linearGradient>
  </defs>

  <rect class="cover-paper" x="280" y="53" width="900" height="1350"/>

  <path class="sky-shape"
        d="M280 53 H1180 V505 A275.6 275.6 0 0 1 730 390 A275.6 275.6 0 0 1 280 505 Z"/>

  <text class="teaser" text-anchor="middle">
    <tspan x="730" y="126">Lorem ipsum dolor sit amet, consectetuer adipiscing</tspan>
    <tspan x="730" y="149">sed diam nonummy nibh euismod tincidunt</tspan>
  </text>

  <rect class="aircraft-slot" x="690" y="200" width="80" height="185" rx="40"
        role="img" aria-label="Helicopter silhouette seen from above, flying upward"/>

  <text class="title-lead" x="730" y="658" text-anchor="middle"
        textLength="230" lengthAdjust="spacingAndGlyphs">STAY</text>

  <g class="speed-lines" stroke="url(#lineFade)">
    <line class="speed-line" x1="296" y1="760" x2="440" y2="760" stroke="url(#lineFade)" stroke-width="6"/>
    <line class="speed-line" x1="310" y1="860" x2="425" y2="860" stroke="url(#lineFade)" stroke-width="4"/>
    <line class="speed-line" x1="300" y1="960" x2="412" y2="960" stroke="url(#lineFade)" stroke-width="8"/>
    <line class="speed-line" x1="318" y1="1060" x2="398" y2="1060" stroke="url(#lineFade)" stroke-width="4"/>
  </g>

  <g class="title-motion" transform="translate(730 1153) skewX(-12) translate(-730 -1153)">
    <text class="title-trail trail-far" x="636" y="1153" text-anchor="middle"
          textLength="500" lengthAdjust="spacingAndGlyphs" aria-hidden="true">BOLD</text>
    <text class="title-trail trail-near" x="658" y="1153" text-anchor="middle"
          textLength="500" lengthAdjust="spacingAndGlyphs" aria-hidden="true">BOLD</text>
    <text class="title-main" x="680" y="1153" text-anchor="middle"
          textLength="500" lengthAdjust="spacingAndGlyphs"
          role="img" aria-label="BOLD, lettering filled with a night city lights scene">BOLD</text>
    <text class="title-glow" x="680" y="1153" text-anchor="middle"
          textLength="500" lengthAdjust="spacingAndGlyphs" aria-hidden="true">BOLD</text>
  </g>

  <rect class="subtitle-band" x="450" y="1164" width="560" height="59"/>
  <text class="subtitle-text" x="730" y="1209" text-anchor="middle"
        textLength="530" lengthAdjust="spacingAndGlyphs">BUILD ON LASTING DISCIPLINE</text>

  <text class="author-name" x="730" y="1339" text-anchor="middle">Dana Whitfield</text>
</svg>
</body>
</html>
```